Dietitian needs awesome business card

I need a contemporary design that's eye catching but professional.
My card is to given to doctors, specialists and patients alike.
I manage patients with chronic diseases
I have uploaded my logo and current business card, I would also like the other Certified Clinical Nutritionist logo incorporated into the design

Target Market(s)

Doctors, specialists and patients

Industry/Entity Type

Healthcare

Contact Information for Business Card

www.brightfieldnutrition.com.au
Ph: 0427 561 903
Fax: 6457 2183
email: marcus.k.diet@fernmail.com
Space on the back of the card with: Appointment date, Appointment time and appointment location

Font styles to use
Serif

Colors
fbee3e
876aae
ffc214

Requirements
Must have
• My Logo
• Certified Clinical Nutritionist Logo
• My 4 locations - Pinebrook Medical Centre, North Corrin Health, Hollis Medical, Ashcombe Doctors Surgery
Nice to have
• I like the colours in my current business card

```html
<!DOCTYPE html>
<html lang="en">
<head>
<meta charset="utf-8">
<title>Marcus Kellaway – Business Card</title>
<link rel="stylesheet" href="https://fonts.googleapis.com/css2?family=Source+Sans+3:wght@400;600&display=swap">
<style>
  :root {
    --page: #ededed;
    --navy: #1c2a8c;
    --blue-mid: #1a78cc;
    --green: #8dc63f;
    --white: #ffffff;
    --ink: #4a4a4a;
    --rule: #a9a9a9;
    --label: #2b3f9a;
    --orange: #f47b20;
    --box: #3a4ea3;
  }
  * { box-sizing: border-box; margin: 0; padding: 0; }
  html, body { width: 1105px; height: 1200px; overflow: hidden; }
  body {
    background: var(--page);
    font-family: "Source Sans 3", "Segoe UI", sans-serif;
    position: relative;
  }
  .card {
    position: absolute;
    left: 179px;
    width: 747px;
    height: 425px;
    overflow: hidden;
  }
  /* Front */
  .card--front {
    top: 119px;
    background:
      linear-gradient(90deg, transparent 0 88%, var(--green) 100%),
      radial-gradient(ellipse at 62% 60%, var(--blue-mid) 0%, #1d53b3 35%, var(--navy) 75%);
  }
  .front__name {
    position: absolute; left: 41px; top: 40px;
    font-size: 27px; font-weight: 400; color: var(--green);
  }
  .front__title {
    position: absolute; left: 41px; top: 76px;
    font-size: 21px; color: var(--white);
  }
  .front__art {
    position: absolute; left: 322px; top: -6px;
    width: 426px; height: 426px; border-radius: 50%;
    background: radial-gradient(circle at 60% 40%, #ffffff 0%, #f2f5fb 60%, #dfe7f5 100%);
  }
  .contact {
    position: absolute; left: 41px; top: 276px;
    list-style: none;
  }
  .contact__item {
    display: flex; align-items: center; gap: 9px;
    height: 29px;
    font-size: 19.5px; color: var(--white);
  }
  .contact__icon { width: 17px; height: 17px; flex: none; }

  /* Back */
  .card--back { top: 636px; background: var(--white); }
  .brand {
    position: absolute; left: 48px; top: 52px;
    display: flex; align-items: center; gap: 12px;
  }
  .brand__dot { width: 58px; height: 58px; border-radius: 50%; background: var(--green); }
  .brand__name {
    font-size: 23px; font-weight: 600; color: var(--navy);
    line-height: 1.05; width: 220px;
  }
  .badge {
    position: absolute; left: 504px; top: 40px;
    width: 178px; height: 83px; background: var(--orange);
    display: flex; align-items: center; justify-content: space-between;
    padding: 0 14px 0 10px;
  }
  .badge__text { color: var(--white); font-size: 13px; line-height: 1.3; width: 95px; }
  .badge__mark { width: 52px; height: 52px; border-radius: 50%; border: 2px solid var(--white); }
  .note-line {
    position: absolute; left: 48px; width: 646px; height: 1px; background: var(--rule);
  }
  .appt {
    position: absolute; left: 48px; top: 272px;
    display: flex; align-items: flex-end;
    font-size: 21px; color: var(--label);
  }
  .appt__field { display: inline-block; border-bottom: 1px solid var(--ink); height: 22px; margin: 0 10px 0 8px; }
  .appt__ampm { font-size: 15px; color: var(--label); margin-left: 2px; }
  .locations {
    position: absolute; left: 48px; top: 330px;
    display: grid; grid-template-columns: 377px 300px; row-gap: 8px;
    list-style: none;
  }
  .location {
    display: flex; align-items: center; gap: 10px;
    font-size: 20px; color: var(--ink);
  }
  .location__box { width: 16px; height: 16px; border: 1.5px solid var(--box); }
</style>
</head>
<body>

<section class="card card--front" aria-label="Business card front">
  <div class="front__art" role="img" aria-label="Large logo illustration: stomach shape with a chef's knife"></div>
  <h1 class="front__name">Marcus Kellaway</h1>
  <p class="front__title">Nutritionist &amp; Chef</p>
  <ul class="contact">
    <li class="contact__item">
      <svg class="contact__icon" viewBox="0 0 24 24"><path fill="#8dc63f" d="M6.6 10.8a15 15 0 0 0 6.6 6.6l2.2-2.2c.3-.3.7-.4 1-.2 1.1.4 2.3.6 3.6.6.6 0 1 .4 1 1V20c0 .6-.4 1-1 1A17 17 0 0 1 3 4c0-.6.4-1 1-1h3.5c.6 0 1 .4 1 1 0 1.3.2 2.5.6 3.6.1.3 0 .7-.2 1z"/></svg>
      0427 561 903
    </li>
    <li class="contact__item">
      <svg class="contact__icon" viewBox="0 0 24 24"><path fill="#8dc63f" d="M6 3h12v5H6zM3 9h18v9h-3v3H6v-3H3zm5 6v4h8v-4z"/></svg>
      6457 2183
    </li>
    <li class="contact__item">
      <svg class="contact__icon" viewBox="0 0 24 24"><path fill="#8dc63f" d="M2 5h20v14H2zm2 2v.5l8 5 8-5V7l-8 5z"/></svg>
      marcus.k.diet@fernmail.com
    </li>
    <li class="contact__item">
      <svg class="contact__icon" viewBox="0 0 24 24"><circle cx="12" cy="12" r="10" fill="#8dc63f"/><path fill="none" stroke="#1c2a8c" stroke-width="1.5" d="M2 12h20M12 2c3 3 3 17 0 20M12 2c-3 3-3 17 0 20"/></svg>
      brightfieldnutrition.com.au
    </li>
  </ul>
</section>

<section class="card card--back" aria-label="Business card back">
  <div class="brand">
    <span class="brand__dot"></span>
    <span class="brand__name">Brightfield Nutrition &amp; Dietetics</span>
  </div>
  <div class="badge">
    <span class="badge__text">Certified Clinical Nutritionist</span>
    <span class="badge__mark"></span>
  </div>
  <div class="note-line" style="top:166px"></div>
  <div class="note-line" style="top:207px"></div>
  <div class="note-line" style="top:248px"></div>
  <div class="appt">
    Date :<span class="appt__field" style="width:305px"></span>
    Time :<span class="appt__field" style="width:143px"></span>
    <span class="appt__ampm">AM/PM</span>
  </div>
  <ul class="locations">
    <li class="location"><span class="location__box"></span>Pinebrook Medical Centre</li>
    <li class="location"><span class="location__box"></span>Ashcombe Doctors Surgery</li>
    <li class="location"><span class="location__box"></span>North Corrin Health</li>
    <li class="location"><span class="location__box"></span>Hollis Medical</li>
  </ul>
</section>

</body>
</html>
```